Lotus Market Hall VIP Card(Magnetic strip plastic card)

We need Fancy,Simple,VIP customer card design for a grocery store name"Lotus Market Hall", Chinese name"福润商场“.Major color should be Dark red. This design is based on a VIP gift card project, which means design should consider about the back side with magnetic strip area and mostly it will be plastic material.

Target Market(s)

Rich Customers

Industry/Entity Type

Grocery Store

Contact Information for Business Card

People actually put more than $1000 into the card for shopping

Font styles to use
Serif
Sans Serif
Decorative
Script
Other font styles liked:
• Fancy

Colors
ec1f27
fbed22

Requirements
Must have
• Red color
Nice to have
• Better logo transformation.

```html
<!DOCTYPE html>
<html lang="en">
<head>
<meta charset="utf-8">
<title>Lotus Market Hall VIP Card</title>
<link rel="stylesheet" href="https://fonts.googleapis.com/css2?family=Arimo:wght@400;700&family=Noto+Sans+SC:wght@700&display=swap">
<style>
  :root {
    --page-bg: #ffffff;
    --card-black: #0b0b0b;
    --dragon-grey: #3a3a3a;
    --brand-red: #ec1f27;
    --brand-yellow: #fbed22;
    --dragon-yellow: #ecd91a;
    --stripe-black: #111111;
    --ink: #1a1a1a;
  }
  * { margin: 0; padding: 0; box-sizing: border-box; }
  html, body { width: 1200px; height: 454px; overflow: hidden; background: var(--page-bg); }
  .canvas { position: relative; width: 1200px; height: 454px; }

  .card {
    position: absolute;
    top: 81px;
    width: 478px;
    height: 329px;
    border-radius: 34px;
    overflow: hidden;
  }
  .card--front { left: 106px; background: var(--card-black); }
  .card--back { left: 615px; background: var(--brand-yellow); }

  .dragon-art { position: absolute; inset: 0; }
  .card--front .dragon-art {
    background: radial-gradient(ellipse at 45% 45%, var(--dragon-grey) 0%, #1d1d1d 45%, var(--card-black) 80%);
    opacity: 0.9;
  }
  .card--back .dragon-art {
    background: radial-gradient(ellipse at 50% 40%, var(--dragon-yellow) 0%, var(--brand-yellow) 70%);
  }

  .brand {
    position: absolute;
    left: 0; right: 0;
    top: 62px;
    display: flex;
    flex-direction: column;
    align-items: center;
  }
  .brand-name-cn,
  .brand-name-en {
    font-family: "Noto Sans SC", "Arimo", sans-serif;
    font-weight: 700;
    color: var(--brand-red);
    line-height: 1;
  }
  .brand-name-cn { font-size: 54px; letter-spacing: 2px; }
  .brand-name-en { font-size: 22px; margin-top: 8px; }
  .tier {
    margin-top: 12px;
    font-family: "Noto Sans SC", "Arimo", sans-serif;
    font-weight: 700;
    font-size: 22px;
    line-height: 1;
    letter-spacing: 4px;
    color: var(--brand-yellow);
  }

  .mag-stripe {
    position: absolute;
    left: 0; right: 0;
    top: 39px;
    height: 36px;
    background: var(--stripe-black);
  }
  .holder-name {
    position: absolute;
    left: 0; right: 0;
    top: 130px;
    text-align: center;
    font-family: "Arimo", sans-serif;
    font-weight: 700;
    font-size: 25px;
    line-height: 1;
    color: var(--ink);
  }
  .terms {
    position: absolute;
    left: 30px; right: 30px;
    top: 196px;
    font-family: "Arimo", sans-serif;
    font-size: 9.2px;
    line-height: 1.3;
    color: var(--ink);
    text-align: left;
  }
  .balance-line {
    position: absolute;
    left: 0; right: 0;
    top: 268px;
    text-align: center;
    font-family: "Arimo", sans-serif;
    font-size: 9.2px;
    color: var(--ink);
  }
</style>
</head>
<body>
<main class="canvas">
  <section class="card card--front" aria-label="Card front">
    <div class="dragon-art" role="img" aria-label="Grey dragon illustration across the black card face"></div>
    <div class="brand">
      <span class="brand-name-cn">福润商场</span>
      <span class="brand-name-en">Lotus Market Hall</span>
      <span class="tier">VIP</span>
    </div>
  </section>

  <section class="card card--back" aria-label="Card back">
    <div class="dragon-art" role="img" aria-label="Faint yellow dragon illustration across the card back"></div>
    <div class="mag-stripe"></div>
    <p class="holder-name">MAYA CHEN</p>
    <p class="terms">CASHIER NOTICE: Photo ID is required to use this VIP Card; the name on the ID must match the name printed on the back of Card. This card is not a credit card and holds no implied warranty. Please present this card to the cashier at time of purchase. Card balance may not be redeemed for cash except where required. The store is not responsible for lost, stolen or damaged Cards. LOST/FIND: if you lose or find this Card please call LMH at 206-555-0142 immediately. Thank you.</p>
    <p class="balance-line">To check your Card Balance anytime call 1-888-555-0199 and input your Card number</p>
  </section>
</main>
</body>
</html>
```